PHGCCUL re-branding website and logo

We are looking for a new webpage design and logo our current page address is www.phgccul-example.org. We want to create a new design using PHGCCUL Pinewood and Harbour Growers Co-operative Credit Union limited and another with the purposed new name PHFC Pinewood and Harbour Financial Co-operative, the color scheme is purple and burnt orange. Our new logo and webpage should communicate change and growth purposed theme continuing our legacy here to server past, present and future generations. Our idea for the logo is a live shot of hands of different ages in a circle holding a tree

Target Market(s)

Everyone

Contact Information for Business Card

Company Name
Telephone number
Address
slot to enter employee info

Logo Text

(P & H) Pinewood And Harbour Financial Co-operative

Coding

Coded - Design and coding required

Number of Pages Required

2 page

Colors
f37122
fbed22
6b449b

Requirements
Must have
• links for social media

```html
<!DOCTYPE html>
<html lang="en">
<head>
<meta charset="utf-8">
<title>Pinewood and Harbour Financial Co-operative</title>
<link href="https://fonts.googleapis.com/css2?family=Montserrat:wght@400;500;600;700;800&display=swap" rel="stylesheet">
<style>
:root{
  --orange:#f37122;
  --yellow:#fbed22;
  --purple:#6b449b;
  --black:#000;
  --ink:#222;
  --muted:#9a9a9a;
  --soft:#f7f7f7;
  --white:#fff;
  --rule-purple:#9a82c0;
}
*{margin:0;padding:0;box-sizing:border-box}
html,body{width:686px;height:1200px;overflow:hidden;background:var(--white)}
body{font-family:'Montserrat',sans-serif;color:var(--ink);position:relative}
.abs{position:absolute}
.utility{top:0;left:0;width:686px;height:20px;font-size:4.8px;color:#444;letter-spacing:.2px}
.utility .links{left:141px;top:8px;white-space:nowrap}
.utility .contact{left:437px;top:8px;white-space:nowrap}
.utility span.sep{margin:0 6px}
.masthead{top:20px;left:0;width:686px;height:53px;background:var(--black)}
.brand{left:141px;top:9px;display:flex;align-items:center;gap:6px}
.brand-mark{width:34px;height:34px;border-radius:50%;background:var(--orange)}
.brand-name{color:var(--white);font-weight:700;font-size:17px;letter-spacing:1px}
.nav{top:0;left:274px;height:53px;display:flex;align-items:center;gap:16px;font-size:5.4px;color:var(--white);font-weight:500;white-space:nowrap}
.btn{background:var(--orange);color:var(--white);font-weight:700;display:flex;align-items:center;justify-content:center;white-space:nowrap}
.login{left:498px;top:18px;width:48px;height:16px;font-size:5.4px}
.hero{top:73px;left:0;width:686px;height:324px;background:linear-gradient(90deg,#5f7d6e 0%,#a9b3ad 35%,#d9d6d0 55%,#2f6f93 80%,#c9c2ba 100%)}
.hero h1{left:140px;top:109px;font-size:25px;line-height:29px;font-weight:800;color:var(--white);white-space:nowrap}
.hero .apply{left:140px;top:188px;width:81px;height:22px;font-size:7.4px}
.dots{left:140px;top:294px;display:flex;gap:7px}
.dots i{width:6px;height:6px;border-radius:50%;background:var(--white)}
.dots i.on{background:var(--yellow)}
.rates{top:397px;left:0;width:686px;height:205px;background:var(--purple);color:var(--white)}
.section-title{width:100%;text-align:center;font-weight:800;font-size:7.2px;letter-spacing:.2px}
.rates .section-title{top:47px}
.rate{top:82px;font-size:6.4px;font-weight:700;line-height:11px;white-space:nowrap}
.rate small{display:block;font-weight:400;color:#b8a2d4;font-size:6px}
.rate b{display:block;color:var(--yellow);font-size:9.4px;font-weight:700;margin-top:4px}
.divider{top:77px;width:1px;height:61px;background:var(--rule-purple)}
.rates .apply{left:295px;top:155px;width:96px;height:22px;font-size:7.2px}
.products{top:602px;left:0;width:686px;height:213px}
.products .section-title{top:45px;color:var(--black)}
.product{top:80px;width:132px}
.product .head{display:flex;align-items:center;gap:8px;font-size:7px;color:var(--black);white-space:nowrap}
.icon{width:33px;height:33px;border-radius:50%;background:var(--orange);display:flex;align-items:center;justify-content:center}
.product p{margin-top:8px;font-size:4.9px;line-height:9px;color:var(--muted);white-space:nowrap}
.pager{font-size:9px;color:#bbb;left:0;width:100%;text-align:center;letter-spacing:4px}
.news{top:815px;left:0;width:686px;height:238px;background:var(--soft)}
.news .section-title{top:34px;color:var(--black)}
.card{top:63px;width:198px;height:119px}
.card .date{left:10px;bottom:7px;color:var(--white);font-weight:800;font-size:8.6px;line-height:8.4px}
.card .caption{left:44px;bottom:12px;color:var(--white);font-size:5px;line-height:9px;width:140px}
.news .pager{top:210px;color:var(--black);font-weight:700;font-size:11px}
.footer{top:1053px;left:0;width:686px;height:147px}
.col{top:31px;font-size:6.6px;line-height:11.5px;color:#444;white-space:nowrap}
.col h4{color:var(--purple);font-size:6.6px;font-weight:700;margin-bottom:11px}
.rule{top:114px;left:12px;width:662px;height:1px;background:#e6e6e6}
.copy{top:125px;left:0;width:686px;text-align:center;font-size:5px;color:#555}
</style>
</head>
<body>
<div class="abs utility">
  <div class="abs links">HOME<span class="sep">|</span>APPLY FOR A LOAN<span class="sep">|</span>BECOME A MEMBER<span class="sep">|</span>LOCATIONS</div>
  <div class="abs contact">PHONE: (555) 418-2730<span class="sep">|</span>FAX: (555) 418-2731</div>
</div>

<header class="abs masthead">
  <div class="abs brand"><span class="brand-mark"></span><span class="brand-name">P &amp; H</span></div>
  <nav class="abs nav"><span>MY CREDIT UNION</span><span>PRODUCTS AND SERVICES</span><span>TOOLS AND BENEFITS</span></nav>
  <div class="abs btn login">LOGIN</div>
</header>

<section class="abs hero" role="img" aria-label="Smiling teacher with arms folded in a classroom with chalkboards">
  <h1 class="abs">Pinewood and Harbour<br>Financial Co-operative</h1>
  <div class="abs btn apply">APPLY LOAN</div>
  <div class="abs dots"><i class="on"></i><i></i><i></i><i></i></div>
</section>

<section class="abs rates">
  <h2 class="abs section-title">FEATURED RATES</h2>
  <div class="abs rate" style="left:141px">Consumer<br>Loans<small>as low as</small><b>9.00% APR*</b></div>
  <div class="abs divider" style="left:220px"></div>
  <div class="abs rate" style="left:244px">New Auto/<br>MotorcycleLoans<small>as low as</small><b>7.00% APR*</b></div>
  <div class="abs divider" style="left:328px"></div>
  <div class="abs rate" style="left:347px">Used Auto/<br>Motorcycle<small>as low as</small><b>11.75% APR*</b></div>
  <div class="abs divider" style="left:426px"></div>
  <div class="abs rate" style="left:451px">Mortgages<small>as low as</small><b style="margin-top:15px">8.25% APR*</b></div>
  <div class="abs btn apply">APPLY FOR A LOAN</div>
</section>

<section class="abs products">
  <h2 class="abs section-title">PRODUCTS AND SERVICES</h2>
  <div class="abs product" style="left:140px">
    <div class="head"><span class="icon"><svg width="18" height="18" viewBox="0 0 18 18" fill="none" stroke="#fff" stroke-width="1.2"><rect x="3" y="4" width="12" height="12" rx="1"/><path d="M7 4V2h4v2M7 8v5M11 8v5"/></svg></span>VACATION CLUB</div>
    <p>Sed ut perspiciatis unde omnis iste natus error sit<br>voluptatem accusantium doloremque<br>laudantium, totam rem aperiam.</p>
  </div>
  <div class="abs product" style="left:279px">
    <div class="head"><span class="icon"><svg width="18" height="18" viewBox="0 0 18 18" fill="none" stroke="#fff" stroke-width="1.2"><circle cx="9" cy="6" r="3"/><path d="M3 16c0-3.5 2.7-6 6-6s6 2.5 6 6"/></svg></span>CONSUMER LOANS</div>
    <p>Sed ut perspiciatis unde omnis iste natus error sit<br>voluptatem accusantium doloremque<br>laudantium, totam rem aperiam.</p>
  </div>
  <div class="abs product" style="left:418px">
    <div class="head"><span class="icon"><svg width="18" height="18" viewBox="0 0 18 18" fill="none" stroke="#fff" stroke-width="1.2"><path d="M2 9l7-6 7 6M4 8v8h10V8M7.5 16v-4h3v4"/></svg></span>MORTGAGES</div>
    <p>Sed ut perspiciatis unde omnis iste natus error sit<br>voluptatem accusantium doloremque<br>laudantium, totam rem aperiam.</p>
  </div>
  <div class="abs pager" style="top:172px">‹ ›</div>
</section>

<section class="abs news">
  <h2 class="abs section-title">NEWS &amp; EVENTS</h2>
  <article class="abs card" style="left:140px;background:linear-gradient(135deg,#8a9a6a,#c79a72 50%,#5c4a3c)" role="img" aria-label="Teacher reading with young pupils in a classroom">
    <div class="abs date">MAR<br>10TH<br>2017</div>
    <div class="abs caption">Sed ut perspiciatis unde omnis iste natus error sit voluptatem accusantium doloremque</div>
  </article>
  <article class="abs card" style="left:347px;background:linear-gradient(135deg,#cfc6b8,#8a7a6a 50%,#3e3a3a)" role="img" aria-label="Group of students and a teacher around a table">
    <div class="abs date">MAR<br>10TH<br>2017</div>
    <div class="abs caption">Sed ut perspiciatis unde omnis iste natus error sit voluptatem accusantium doloremque</div>
  </article>
  <div class="abs pager">‹ ›</div>
</section>

<footer class="abs footer">
  <div class="abs col" style="left:117px"><h4>Northbay</h4>Harbour Road &amp; Pinecrest Dr.<br>Phone: (555) 418-2730<br>Fax: (555) 418-2731</div>
  <div class="abs col" style="left:247px"><h4>Westport, Grand Cay</h4>#8 West Seaview Dr.<br>Phone: (555) 604-7152<br>Fax: (555) 604-7153</div>
  <div class="abs col" style="left:372px"><h4>Pine Cay</h4>Harbour Pines Shopping Centre<br>Phone: (555) 739-0264<br>Fax: (555) 739-0265</div>
  <div class="abs col" style="left:499px"><h4>Other Links</h4>Privacy Policy<br>Website Terms<br>USA Patriot Act</div>
  <div class="abs rule"></div>
  <div class="abs copy">Copyright © 2017 Pinewood and Harbour Financial Co-operative. All Rights Reserved.</div>
</footer>
</body>
</html>
```